holloway paving service

Needs to have phone number 0418259730 and email markholloway@brightmail.com.au.
ABN 62318470915
name mark holloway

For all your concreting solutions
Excavation
Exposed & colour concrete
House & shed slabs
Driveways
Landing & steps

Contact Information for Business Card

ph 0418259730
email markholloway@brightmail.com.au.
ABN 62318470915
name mark holloway

```html
<!DOCTYPE html>
<html lang="en">
<head>
<meta charset="utf-8">
<title>Holloway Paving Service – Business Card</title>
<link rel="stylesheet" href="https://fonts.googleapis.com/css2?family=Poppins:wght@400;500;600&display=swap">
<style>
  :root {
    --page-bg: #d9d5d1;
    --card-bg: #ececec;
    --card-edge: #c9c9c9;
    --charcoal: #3a3a3c;
    --text-dark: #2b2b2b;
    --orange: #d8461f;
    --dots: #6d6d6d;
  }
  * { box-sizing: border-box; margin: 0; padding: 0; }
  html, body {
    width: 1200px;
    height: 969px;
    overflow: hidden;
    background: var(--page-bg);
    font-family: "Poppins", sans-serif;
  }
  .business-card {
    position: absolute;
    left: 100px;
    top: 200px;
    width: 1000px;
    height: 568px;
    background: var(--card-bg);
    border: 1px solid var(--card-edge);
    box-shadow: 0 10px 30px rgba(0,0,0,0.18);
    overflow: hidden;
  }
  .brand-mark {
    position: absolute;
    left: 70px;
    top: 200px;
    display: flex;
    align-items: center;
    gap: 22px;
  }
  .brand-mark__square {
    width: 64px;
    height: 64px;
    background: var(--orange);
  }
  .brand-mark__name {
    font-weight: 600;
    font-size: 30px;
    line-height: 1.15;
    color: var(--charcoal);
    text-transform: uppercase;
    width: 270px;
  }
  .contact-block {
    position: absolute;
    right: 58px;
    top: 40px;
    width: 520px;
    text-align: right;
  }
  .contact-block__name {
    font-weight: 600;
    font-size: 36px;
    color: var(--orange);
    text-transform: uppercase;
    line-height: 1.1;
  }
  .contact-block__line {
    font-size: 23px;
    color: var(--text-dark);
    line-height: 1.35;
    margin-top: 2px;
  }
  .dotted-rule {
    position: absolute;
    right: 58px;
    width: 300px;
    border-top: 3px dotted var(--dots);
  }
  .dotted-rule--top { top: 176px; }
  .dotted-rule--bottom { top: 384px; }
  .service-list {
    position: absolute;
    right: 58px;
    top: 200px;
    list-style: none;
    text-align: right;
  }
  .service-list__item {
    font-size: 23px;
    line-height: 30px;
    color: var(--text-dark);
  }
  .service-list__item::after {
    content: "";
    display: inline-block;
    width: 8px;
    height: 8px;
    background: var(--orange);
    transform: rotate(45deg);
    margin-left: 18px;
    vertical-align: middle;
    position: relative;
    top: -2px;
  }
  .company-block {
    position: absolute;
    right: 58px;
    top: 402px;
    width: 520px;
    text-align: center;
  }
  .company-block__name {
    font-weight: 600;
    font-size: 34px;
    color: var(--orange);
    text-transform: uppercase;
    line-height: 1.1;
    text-align: right;
  }
  .company-block__tag {
    display: flex;
    align-items: center;
    gap: 16px;
    margin: 6px 0 0 34px;
    font-weight: 500;
    font-size: 26px;
    letter-spacing: 4px;
    color: var(--text-dark);
    text-transform: uppercase;
  }
  .company-block__tag::before,
  .company-block__tag::after {
    content: "";
    flex: 1;
    border-top: 3px solid var(--charcoal);
  }
  .company-block__phone {
    font-size: 27px;
    letter-spacing: 3px;
    color: var(--orange);
    margin-left: 34px;
    text-align: left;
    padding-left: 14px;
  }
</style>
</head>
<body>
  <div class="business-card">
    <div class="brand-mark">
      <div class="brand-mark__square"></div>
      <div class="brand-mark__name">Holloway Paving Service</div>
    </div>

    <div class="contact-block">
      <div class="contact-block__name">Mark Holloway</div>
      <div class="contact-block__line">markholloway@brightmail.com.au</div>
      <div class="contact-block__line">ABN 62318470915</div>
    </div>

    <div class="dotted-rule dotted-rule--top"></div>

    <ul class="service-list">
      <li class="service-list__item">Excavation</li>
      <li class="service-list__item">Exposed &amp; colour concrete</li>
      <li class="service-list__item">House &amp; shed slabs</li>
      <li class="service-list__item">Driveways</li>
      <li class="service-list__item">Landing &amp; steps</li>
    </ul>

    <div class="dotted-rule dotted-rule--bottom"></div>

    <div class="company-block">
      <div class="company-block__name">Holloway Paving</div>
      <div class="company-block__tag">Service</div>
      <div class="company-block__phone">0418259730</div>
    </div>
  </div>
</body>
</html>
```